brightwell - Property Management DL Card

I am after a savvy designer to cut through junk mail! so many real estate agents use flyers to promote themselves and their business and usually sales. We are a property management firm (residential) and we want to represent landlords that have existing investment properties and need a quality agent to represent them. Can you help?
DL size, will be printed and delivered to mailboxes. For a look at our website go to www.brightwellrs.com.au. Keep it simple and clutter free.
it is to be double sided - with one side to be simple and clear - just our website, logo and telephone number on the back.
attached is our logo and our telephone number is 1300 48 92 16
the above are 2 essential elements to be included + our email address: admin@brightwellrs.com.au
also attached are our transparent price list

Target Market(s)
property investors,
people that manage properties themselves
Industry/Entity Type
Property Management
- arial
Look and feel

```html
<!DOCTYPE html>
<html lang="en">
<head>
<meta charset="utf-8">
<title>brightwell – Property Management DL Card</title>
<link rel="stylesheet" href="https://fonts.googleapis.com/css2?family=Open+Sans:wght@300;400;600&display=swap">
<style>
  :root {
    --page-bg: #e6e6e6;
    --card-taupe: #c6c1b6;
    --card-back: #b2ab9b;
    --panel-white: #ffffff;
    --ink: #2f2f2f;
    --ink-soft: #3b362f;
    --bullet-grey: #9a9a9a;
    --bar-black: #111111;
    --banner-text: #d9d9d9;
    --photo-dark: #6e6b67;
    --photo-light: #d8d2c8;
  }
  * { box-sizing: border-box; margin: 0; padding: 0; }
  html, body { width: 1200px; height: 1200px; overflow: hidden; }
  body {
    background: var(--page-bg);
    font-family: "Open Sans", Arial, sans-serif;
    position: relative;
  }

  /* Front side */
  .card-front {
    position: absolute; left: 120px; top: 55px;
    width: 1000px; height: 500px;
    background: var(--card-taupe);
    overflow: hidden;
  }
  .interior-photo {
    position: absolute; left: 0; top: 0;
    width: 668px; height: 500px;
    background: linear-gradient(160deg, var(--photo-light) 0%, #b9b2a8 50%, var(--photo-dark) 100%);
  }
  .photo-frame {
    position: absolute; left: 0; top: 0;
    width: 668px; height: 500px;
    border: 23px solid rgba(198,193,182,0.55);
    border-right: none;
  }
  .info-panel {
    position: absolute; left: 669px; top: 23px;
    width: 309px; height: 454px;
    background: var(--panel-white);
  }
  .tagline-bar {
    position: absolute; left: 420px; top: 117px;
    width: 545px; height: 27px;
    background: linear-gradient(90deg, rgba(17,17,17,0) 0%, rgba(17,17,17,0.85) 18%, var(--bar-black) 40%, var(--bar-black) 72%, rgba(17,17,17,0.6) 86%, rgba(17,17,17,0) 100%);
  }
  .tagline {
    position: absolute; left: 533px; top: 116px;
    height: 27px; line-height: 27px;
    font-size: 18px; font-weight: 600;
    color: var(--banner-text);
    letter-spacing: 0.3px;
  }
  .benefit-list {
    position: absolute; left: 698px; top: 156px;
    list-style: none;
  }
  .benefit-list li {
    font-size: 16.5px; color: var(--ink);
    line-height: 21.7px;
    padding-left: 16px; position: relative;
  }
  .benefit-list li::before {
    content: ""; position: absolute; left: 1px; top: 7px;
    width: 7px; height: 7px;
    background: var(--bullet-grey);
    transform: rotate(45deg);
  }
  .front-wordmark {
    position: absolute; left: 749px; top: 388px;
    font-size: 38px; font-weight: 300;
    color: var(--ink); letter-spacing: -0.5px;
  }

  /* Back side */
  .card-back {
    position: absolute; left: 119px; top: 637px;
    width: 1002px; height: 500px;
    background: var(--card-back);
  }
  .wordmark-bar {
    position: absolute; left: 36px; top: 51px;
    width: 366px; height: 69px;
    background: linear-gradient(90deg, rgba(17,17,17,0) 0%, rgba(17,17,17,0.9) 14%, var(--bar-black) 30%, var(--bar-black) 70%, rgba(17,17,17,0.9) 84%, rgba(17,17,17,0) 100%);
  }
  .back-wordmark {
    position: absolute; left: 26px; top: 51px;
    width: 366px; height: 69px; line-height: 66px;
    text-align: center;
    font-size: 34px; font-weight: 300;
    color: #ffffff; letter-spacing: -0.3px;
  }
  .contact-block {
    position: absolute; left: 555px; top: 377px;
    border-left: 2px solid var(--ink-soft);
    padding-left: 19px;
    font-size: 18px; line-height: 24.5px;
    font-style: normal;
    color: var(--ink-soft);
    letter-spacing: 0.3px;
  }
</style>
</head>
<body>
  <section class="card-front">
    <div class="interior-photo" role="img" aria-label="Photo of a bright modern living room with white sofas, a dark rug and floor-to-ceiling windows at sunset"></div>
    <div class="photo-frame"></div>
    <div class="info-panel"></div>
    <div class="tagline-bar"></div>
    <p class="tagline">Property Management specialists</p>
    <ul class="benefit-list">
      <li>Excellent communication</li>
      <li>No hidden extras</li>
      <li>Minimal vacancy</li>
      <li>The best rent return</li>
    </ul>
    <p class="front-wordmark">brightwell</p>
  </section>

  <section class="card-back">
    <div class="wordmark-bar"></div>
    <p class="back-wordmark">brightwell</p>
    <address class="contact-block">
      <div>1300 48 92 16</div>
      <div>PO Box B527, Northgate NSW, 2161</div>
      <div>admin@brightwellrs.com.au</div>
    </address>
  </section>
</body>
</html>
```